Build Distinctive Business Card: Public Relations Government Relations firm

I have logo and colors done (attached) need a very cool way to present it on a business card (can be two sided if need be).

Public Relations Government Relations firm

Info:

Paul Marchetti, CEO
Keystone Public Relations
2730 West Harlan Blvd.
Los Angeles CA 90012
(o) 213.555.0148
(f) 213.555.0173
paul@keystonekpr-example.com

Target Market(s)

Government relations, public relations, lobbyist, I was a past State Senator

Industry/Entity Type

Business

Contact Information for Business Card

Info:

Paul Marchetti, CEO
Keystone Public Relations
2730 West Harlan Blvd.
Los Angeles CA 90012
(o) 213.555.0148
(f) 213.555.0173
paul@keystonekpr-example.com
@paulmarchetti

Requirements
Must have
• A sense of balance given logo is already done.
• It's a government relations firm really.
• Lobbyist type.
• Senatorial type...

```html
<!DOCTYPE html>
<html lang="en">
<head>
<meta charset="utf-8">
<title>Keystone Public Relations – Business Card</title>
<link rel="stylesheet" href="https://fonts.googleapis.com/css2?family=Open+Sans:wght@300;400;700&display=swap">
<style>
  :root {
    --ink: #111111;
    --ink-soft: #2a2a2a;
    --paper: #f7f7f7;
    --paper-shade: #e4e4e4;
    --rule: #9a9a9a;
    --muted: #6e6e6e;
    --white: #ffffff;
    --stage: #d9d6d1;
  }
  * { margin: 0; padding: 0; box-sizing: border-box; }
  html, body { width: 1200px; height: 885px; overflow: hidden; }
  body {
    background: var(--stage);
    font-family: "Open Sans", sans-serif;
    position: relative;
  }
  .card {
    position: absolute;
    width: 540px;
    height: 309px;
    border-radius: 3px;
    overflow: hidden;
    box-shadow: 0 10px 30px rgba(0,0,0,.25);
  }

  /* Front */
  .card-front {
    left: 50px; top: 120px;
    background: linear-gradient(160deg, var(--white) 0%, var(--paper) 60%, var(--paper-shade) 100%);
  }
  .front-band {
    position: absolute; left: 0; top: 0; bottom: 0; width: 100px;
    background: linear-gradient(90deg, var(--ink), var(--ink-soft));
  }
  .brand {
    position: absolute; display: flex; align-items: center; gap: 10px;
  }
  .brand-mark {
    width: 70px; height: 70px; border-radius: 50%;
    background: var(--ink); border: 5px solid var(--white);
    box-shadow: 0 0 0 3px var(--ink);
    flex: none;
  }
  .brand-name {
    font-weight: 700; font-size: 40px; line-height: 1; letter-spacing: -0.5px;
  }
  .brand-tag {
    font-weight: 400; font-size: 9px; letter-spacing: 3px; text-transform: uppercase;
    margin-top: 5px;
  }
  .card-front .brand { left: 64px; top: 150px; }
  .card-front .brand-name { color: var(--ink); }
  .card-front .brand-tag { color: var(--muted); }

  .contact-block {
    position: absolute; right: 24px; top: 28px; width: 232px;
    color: var(--ink);
  }
  .person {
    font-weight: 400; font-size: 21px; line-height: 1.1;
    padding-bottom: 6px; border-bottom: 1px solid var(--rule);
  }
  .person .role { font-size: 14px; color: var(--muted); font-weight: 300; }
  .contact-list { list-style: none; margin-top: 8px; }
  .contact-list li {
    display: flex; align-items: center; gap: 8px;
    font-weight: 300; font-size: 14px; line-height: 23px;
  }
  .contact-list svg { width: 13px; height: 13px; flex: none; }

  .address {
    position: absolute; right: 24px; bottom: 28px; width: 232px;
    font-weight: 300; font-size: 14px; line-height: 20px; color: var(--ink);
  }

  /* Back */
  .card-back {
    left: 610px; top: 460px;
    background: radial-gradient(ellipse at 35% 30%, #2c2c2c 0%, var(--ink) 65%);
  }
  .back-ring {
    position: absolute; left: 150px; top: -20px;
    width: 350px; height: 350px; border-radius: 50%;
    border: 28px solid rgba(255,255,255,.05);
  }
  .card-back .brand { left: 100px; top: 112px; }
  .card-back .brand-name { color: var(--white); font-size: 50px; }
  .card-back .brand-tag { color: #cfcfcf; font-size: 10px; letter-spacing: 3.4px; }
</style>
</head>
<body>

  <section class="card card-front" aria-label="Business card front">
    <div class="front-band"></div>

    <div class="brand">
      <div class="brand-mark"></div>
      <div>
        <div class="brand-name">Keystone</div>
        <div class="brand-tag">Public Relations</div>
      </div>
    </div>

    <div class="contact-block">
      <p class="person">Paul Marchetti <span class="role">| CEO</span></p>
      <ul class="contact-list">
        <li>
          <svg viewBox="0 0 13 13" aria-hidden="true"><rect width="13" height="13" fill="#111"/><path d="M3 4c1 3 3 5 6 6l1-1.5-2-1-1 .8c-1-.6-1.8-1.4-2.3-2.3l.8-1-1-2z" fill="#fff"/></svg>
          213.555.0148
        </li>
        <li>
          <svg viewBox="0 0 13 13" aria-hidden="true"><rect width="13" height="13" fill="#111"/><path d="M3 4c1 3 3 5 6 6l1-1.5-2-1-1 .8c-1-.6-1.8-1.4-2.3-2.3l.8-1-1-2z" fill="#fff"/></svg>
          213.555.0173
        </li>
        <li>
          <svg viewBox="0 0 13 13" aria-hidden="true"><rect x=".5" y=".5" width="12" height="12" fill="#fff" stroke="#111"/><path d="M2 3l9 7M11 3l-9 7" stroke="#111" stroke-width="1.2"/></svg>
          paul@keystonekpr-example.com
        </li>
      </ul>
    </div>

    <p class="address">2730 West Harlan Blvd.<br>Los Angeles CA 90012</p>
  </section>

  <section class="card card-back" aria-label="Business card back">
    <div class="back-ring"></div>
    <div class="brand">
      <div class="brand-mark"></div>
      <div>
        <div class="brand-name">Keystone</div>
        <div class="brand-tag">Public Relations</div>
      </div>
    </div>
  </section>

</body>
</html>
```